Etiketten-Design für Weine
Zielgruppe
Wir sind ein kleines Familien-Weingut Nahe Bernkastel-Kues an der Mosel. Wir erzeugen auf 5,5ha ca. 40-50 TSD Flaschen Wein. Dabei legen wir Wert auf eine naturnahe Bewirtschaftung und eine gute Qualität der Weine. Die wichtigste Rebsorte ist der Riesling. Ansonsten steht die Mosel vor allem für Schieferstein, Steillagen, schöne Landschaft. Die Vermarktung erfolgt fast ausschließlich an Privatkunden. Die Kunden sind i. d. R. mind. 40 Jahre bis 70 Jahre alt gehören mind. der Mittelschicht an; Akademiker und Personen mit Dr.-Titel sind stärker repräsentiert als im Bundesdurchschnitt. Die Vermarktung ist stark Personengebunden: Ich als Winzer bin meist persönlich im Gespräch mit den Kunden.
Aufgabenstellung
Bei dem Entwurf geht es mehr um eine 'kleinen Relaunch'. Bevor Anfang Januar 2021 neue Etiketten gedruckt werden für den neuen Jahrgang, soll das Design nochmals überdacht werden. Hin und wieder werde ich angesprochen von Seiten der Kundschaft; das bisherige Etikett wird anscheinend eher als altbacken wahrgenommen.
Grundsätzlich besteht das Etikett aus dem Logo (farbiger Balken, Hauszeichnung, Schriftzug Brucker-Hamm) und dem weißen Feld mit der Weinbezeichnung darunter. Für den goldenen Rahmen und den Schriftzug Brucker-Hamm wird Heißfolienprägung verwendet. Grün=Basisweine/Literflasche; rot=Hauptlinie ; lila=Premiumlinie ; schwarz=nur für den Rotwein ; Paul am Bach (Perlwein) ist ein Sonderetikett mit einem Acrylbild und der Erdquelle Traubensaft erhält jedes Jahr eine neues Foto der Traubenleser. Die stets verwendete Schriftart ist Windows Garamond.
Grundsätzlich würde ich an dem Logo (farbiger Balken mit Hauszeichnung und Schriftzug Weingut Brucker-Hamm) eigentlich gerne festhalten. Da dieses Logo bereits überall Verwendung findet (Broschüre, Visitenkarten, Briefbogen, Weingläser, Weinstand, Website, etc.). Lediglich der goldene Rahmen steht zur Disposition (der findet - außer beim Etikett - sonst keine Verwendung). Gestaltungsmöglichkeit sehe ich in dem weißen Feld unter dem Logo. Da bin ich für alles offen. Mögliche Ansatzpunkte wären Herkunft oder Personen oder einfach grafische Elemente/Effekte um das Etikett aufzuwerten. Da ich bereits mit den verschiedenen Farben (grün/rot/lila/schwarz) arbeite, würde ich an dieser Stelle nicht zusätzlich weitere Farben ins Spiel bringen. Wichtig sind mir die prägnanten Weinnamen (Marktgeflüster, Sonne Vier, Ruhepol, Feiner Krug, usw.) Die gesetzlich notwendigen Angaben befinden sich jedoch auf dem Rückenetikett. Das gesamte Weinsortiment kann auch angeschaut werden im Shop unter www.brucker-hamm.de

```html
<!DOCTYPE html>
<html lang="de">
<head>
<meta charset="utf-8">
<title>Paul am Bach – Muscaris Secco Etikett</title>
<link rel="stylesheet" href="https://fonts.googleapis.com/css2?family=EB+Garamond:wght@500&family=Inter:wght@300;400&display=swap">
<style>
  :root {
    --canvas-bg: #f7f7f7;
    --band-red: #9b2a45;
    --foil-gold: #e6cf9c;
    --sky-blue: #9fc4e0;
    --feather-white: #eeeef0;
    --water-teal: #4f8c8a;
    --field-white: #fbfbfb;
    --ink-dark: #3a3a3a;
    --ink-soft: #7a7a7a;
  }
  * { margin: 0; padding: 0; box-sizing: border-box; }
  html, body {
    width: 800px;
    height: 1200px;
    overflow: hidden;
    background: var(--canvas-bg);
  }
  .canvas {
    position: relative;
    width: 800px;
    height: 1200px;
  }
  .label {
    position: absolute;
    left: 80px;
    top: 117px;
    width: 640px;
    height: 966px;
    box-shadow: 0 2px 10px rgba(0,0,0,0.08);
  }
  .brand-band {
    position: absolute;
    left: 0; top: 0;
    width: 100%;
    height: 201px;
    background: var(--band-red);
  }
  .brand-mark {
    position: absolute;
    left: 118px;
    top: 62px;
    width: 78px;
    height: 78px;
    border: 1.5px solid var(--foil-gold);
  }
  .brand-name {
    position: absolute;
    left: 278px;
    top: 52px;
    font-family: "EB Garamond", Garamond, serif;
    font-weight: 500;
    color: var(--foil-gold);
    font-size: 34px;
    line-height: 44px;
  }
  .artwork {
    position: absolute;
    left: 0; top: 201px;
    width: 100%;
    height: 765px;
    background: linear-gradient(180deg,
      var(--sky-blue) 0%,
      #c8dcea 22%,
      var(--feather-white) 45%,
      #dedfe4 68%,
      var(--water-teal) 100%);
  }
  .wine-field {
    position: absolute;
    left: 122px;
    top: 575px;
    width: 393px;
    height: 160px;
    background: var(--field-white);
    text-align: center;
    padding-top: 50px;
    font-family: "Inter", Arial, sans-serif;
    font-size: 26px;
    line-height: 34px;
    letter-spacing: 0.14em;
  }
  .wine-name { color: var(--ink-dark); font-weight: 400; }
  .wine-type { color: var(--ink-soft); font-weight: 300; }
</style>
</head>
<body>
  <div class="canvas">
    <div class="label">
      <header class="brand-band">
        <div class="brand-mark"></div>
        <div class="brand-name">Weingut<br>Brucker-Hamm</div>
      </header>
      <div class="artwork" role="img" aria-label="Acrylbild: weiße Gänse mit ausgebreiteten Flügeln vor blauem Himmel"></div>
      <div class="wine-field">
        <p class="wine-name">Paul am Bach</p>
        <p class="wine-type">Muscaris Secco</p>
      </div>
    </div>
  </div>
</body>
</html>
```